Amber Vital 480

This is a 9 week program we conduct in our gym/recovery facility with the aim of educating members on the ins and outs of training, sauna use, cold plunge, sleep and lifestyle factors that they need to consider to increase health span into their older age. It is geared towards the Gen X age group.

```html
<!DOCTYPE html>
<html lang="en">
<head>
<meta charset="utf-8">
<title>Amber Vital 480 — Home Page Variants</title>
<link href="https://fonts.googleapis.com/css2?family=Montserrat:wght@600;700;800&family=Lato:wght@400;700&display=swap" rel="stylesheet">
<style>
  :root{
    --stage:#e4e4e4;
    --ink:#111418;
    --body:#3d4147;
    --blue:#0a6cf0;
    --sky:#0aa2f5;
    --hero-bg:#e7f7fd;
    --soft:#f4f4f4;
    --footer:#333333;
    --white:#ffffff;
    --star:#f5a623;
  }
  *{box-sizing:border-box;margin:0;padding:0}
  html,body{width:895px;height:1200px;overflow:hidden;background:var(--stage)}
  body{position:relative;font-family:"Lato",Arial,sans-serif;color:var(--body)}
  .page{position:absolute;top:22.8px;width:758px;height:2118px;background:var(--white);transform:scale(0.5418);transform-origin:0 0;overflow:hidden;box-shadow:0 2px 8px rgba(0,0,0,.08)}
  .page--a{left:23.3px}
  .page--b{left:454.6px}
  .abs{position:absolute}
  .heading{font-family:"Montserrat",Arial,sans-serif;font-weight:700;color:var(--ink)}
  .accent{color:var(--blue)}
  .rule{position:absolute;height:2px;width:44px;background:var(--blue)}
  .btn{position:absolute;display:flex;align-items:center;justify-content:center;border-radius:14px;font-family:"Montserrat",Arial,sans-serif;font-weight:700;font-size:9.5px;background:var(--blue);color:var(--white)}

  /* nav */
  .brand{left:70px;top:20px;font-family:"Montserrat",Arial,sans-serif;font-weight:800;font-size:19px;color:var(--ink)}
  .nav{left:277px;top:25px;display:flex;gap:0;font-size:10px;color:var(--ink)}
  .nav a{text-decoration:none;color:inherit;margin-right:34px}
  .nav a.active{color:var(--blue);font-weight:700}
  .nav-cta{left:612px;top:18px;width:76px;height:24px;border-radius:12px}

  /* hero */
  .hero{left:18px;top:62px;width:722px;height:324px;background:var(--hero-bg)}
  .hero-kicker{left:70px;top:130px;font-size:11px;font-weight:700;color:var(--ink)}
  .hero-title{left:68px;top:148px;font-size:36px;font-weight:800}
  .hero-sub{left:70px;top:199px;font-size:10px;color:var(--blue)}
  .hero-text{left:70px;top:226px;width:260px;font-size:9.8px;line-height:17px}
  .hero-btn{left:70px;top:288px;width:91px;height:26px}
  .hero-photo{left:435px;top:98px;width:251px;height:251px;border-radius:125px 125px 125px 0}
  .photo-warm{background:linear-gradient(140deg,#f1b26a 0%,#c47a45 45%,#5a4a3e 100%)}
  .photo-office{background:linear-gradient(140deg,#c8d4de 0%,#6d7f92 50%,#2c3e55 100%)}
  .hero-vert{left:707px;top:385px;transform:rotate(-90deg);transform-origin:0 0;font-family:"Montserrat",Arial,sans-serif;font-weight:800;font-size:42px;letter-spacing:1px;color:rgba(255,255,255,.85);white-space:nowrap}

  /* about */
  .tile{position:absolute;border-radius:3px}
  .about-title{left:379px;top:434px;font-size:24px}
  .about-text{left:379px;width:312px;font-size:9.5px;line-height:16.3px}
  .about-more{left:379px;top:677px;width:80px;height:26px}

  /* services */
  .services{left:0;top:754px;width:758px;height:401px;background:var(--soft)}
  .center-title{left:0;width:758px;text-align:center;font-size:24px}
  .svc{position:absolute;top:850px;width:190px;height:248px}
  .svc-panel{position:absolute;left:0;top:20px;width:190px;height:228px;background:var(--sky)}
  .svc--active .svc-panel{background:var(--blue);box-shadow:0 6px 14px rgba(10,108,240,.35)}
  .svc-photo{position:absolute;left:20px;top:0;width:170px;height:153px}
  .svc-week{position:absolute;left:18px;top:162px;font-size:8px;font-weight:700;color:var(--white)}
  .svc-name{position:absolute;left:18px;top:177px;font-family:"Montserrat",Arial,sans-serif;font-weight:700;font-size:11px;color:var(--white)}
  .svc-text{position:absolute;left:18px;top:196px;width:160px;font-size:8px;line-height:15px;color:rgba(255,255,255,.92)}
  .svc-icon{position:absolute;right:14px;top:160px}
  .arrow{position:absolute;top:964px;width:22px;height:22px}

  /* quote band */
  .quote{left:0;top:1155px;width:758px;height:261px;background:linear-gradient(120deg,#0aa3f6 0%,#0a95f2 55%,#0a6cf0 100%);overflow:hidden}
  .quote-curve{position:absolute;left:0;top:0}
  .quote-title{left:0;top:1189px;width:758px;text-align:center;font-size:22px;color:var(--white)}
  .quote-text{left:100px;width:558px;text-align:center;font-size:9.5px;line-height:17px;color:var(--white)}
  .q-btn-light{left:258px;top:1342px;width:80px;height:26px;background:var(--white);color:var(--blue)}
  .q-btn-line{left:355px;top:1342px;width:145px;height:26px;background:transparent;border:1.3px solid var(--white)}

  /* reviews */
  .review{position:absolute;top:1538px;width:190px;height:122px;background:var(--white);box-shadow:0 2px 10px rgba(0,0,0,.09);text-align:center}
  .avatar{position:absolute;left:73px;top:-22px;width:44px;height:44px;border-radius:50%;border:3px solid var(--white);background:linear-gradient(160deg,#d9c3ad,#7d6a5c);box-shadow:0 1px 4px rgba(0,0,0,.15)}
  .review-name{margin-top:33px;font-size:10.5px;font-weight:700;color:var(--ink)}
  .stars{font-size:6.5px;letter-spacing:1px;color:var(--star);margin-top:2px}
  .review-text{margin:4px auto 0;width:172px;font-size:8.5px;line-height:16px}
  .pager{left:341px;top:1696px;display:flex;gap:6px}
  .pager i{display:block;width:7px;height:7px;border-radius:50%;background:#cfe0f7}
  .pager i.on{background:var(--blue)}

  /* footer */
  .footer{left:0;top:1762px;width:758px;height:356px;background:var(--footer);color:var(--white)}
  .field{position:absolute;top:1811px;width:117px;height:31px;border-radius:16px;background:var(--white);font-size:9px;font-weight:700;color:var(--ink);padding-left:13px;display:flex;align-items:center}
  .submit{left:571px;top:1811px;width:117px;height:31px;border-radius:16px;font-size:11px;background:linear-gradient(90deg,#0a6cf0,#0a9cf3)}
  .fline{position:absolute;left:70px;width:618px;height:1px;background:#4e4e4e}
  .f-brand{left:70px;top:1898px;font-family:"Montserrat",Arial,sans-serif;font-weight:800;font-size:21px;color:var(--white)}
  .f-col{top:1902px;font-size:9px;color:#e9e9e9}
  .f-col h4{font-family:"Montserrat",Arial,sans-serif;font-size:12px;font-weight:700;color:var(--white);margin-bottom:10px}
  .f-col li{list-style:none;line-height:21.8px}
  .f-contact li{display:flex;align-items:center;gap:9px;margin-bottom:13px;line-height:16px}
  .dot-ico{flex:none;width:19px;height:19px;border-radius:50%;background:var(--blue);display:flex;align-items:center;justify-content:center}
  .copy{left:0;top:2087px;width:758px;text-align:center;font-size:9px;color:#e9e9e9}
</style>
</head>
<body>

<!-- Variant A -->
<section class="page page--a" aria-label="Home page, variant with outdoor couple photo">
  <div class="abs brand">Amber Vital 480</div>
  <nav class="abs nav"><a class="active" href="#">Home</a><a href="#">About</a><a href="#">Services</a><a href="#">Reviews</a><a href="#">Blog</a></nav>
  <div class="btn nav-cta">Contact Us</div>

  <div class="abs hero"></div>
  <div class="abs hero-vert">AMBER VITAL</div>
  <div class="abs hero-kicker">Welcome to</div>
  <h1 class="abs heading hero-title">Amber Vital 480</h1>
  <div class="abs hero-sub">9-WEEK PROGRAM WE CONDUCT</div>
  <div class="rule" style="left:70px;top:215px;width:40px"></div>
  <p class="abs hero-text">Lorem ipsum dolor sit amet, consectetur adipiscing elit, sed do eiusmod tempor incididunt ut labore et dolore magna aliqua.</p>
  <div class="btn hero-btn">Get Started</div>
  <div class="abs hero-photo photo-warm" role="img" aria-label="Smiling middle-aged couple outdoors at sunset"></div>

  <div class="tile" style="left:70px;top:442px;width:129px;height:258px;background:linear-gradient(160deg,#b08a66,#5e6f80)" role="img" aria-label="Coach meeting with a member at a laptop"></div>
  <div class="tile" style="left:203px;top:442px;width:128px;height:184px;background:linear-gradient(160deg,#c9c2b8,#8b7f70)" role="img" aria-label="Two women reviewing a tablet"></div>
  <div class="tile" style="left:203px;top:630px;width:128px;height:70px;background:linear-gradient(160deg,#a59a8f,#6b625a)" role="img" aria-label="Older couple embracing"></div>
  <h2 class="abs heading about-title"><span class="accent">About</span> Amber Vital 480</h2>
  <div class="rule" style="left:379px;top:467px;width:44px"></div>
  <p class="abs about-text" style="top:476px">Lorem ipsum dolor sit amet, consectetur adipiscing elit, sed do eiusmod incididunt ut labore et dolore magna aliqua. Ut enim ullamco laboris nisi aliquip ex ea commodoad minim venm, quis nostrud exercitation ullmco laboris nisi ut aliquip ex ea commodo consequat.</p>
  <p class="abs about-text" style="top:557px">Duis aute irure dolor in reprehenderit in voluptate velit esse cillum sunt culpa qui officia deserunt mollit anim id est laborum doloe eu fugiat nulla pariatur. Excepteur sint occaecat cupidatat non proident, sunt in culpa qui officia deserunt mollit anim id est laborum. Ut enim ad minim veniam, quis nostrud exercitation ullamco laboris nisi ut aliquip ex ea commodo consequat. Duis aute irure dolor in reprehenderit in voluptate velit esse cillum dolore eu fugiat nulla pariatur.</p>
  <div class="btn about-more">Read More</div>

  <div class="abs services"></div>
  <h2 class="abs heading center-title" style="top:788px"><span class="accent">Our</span> Services</h2>
  <div class="rule" style="left:357px;top:820px"></div>
  <svg class="arrow" style="left:23px" viewBox="0 0 22 22"><circle cx="11" cy="11" r="10" fill="none" stroke="#222" stroke-width="1"/><path d="M15 11H7M10 8l-3 3 3 3" fill="none" stroke="#222" stroke-width="1"/></svg>
  <svg class="arrow" style="left:710px" viewBox="0 0 22 22"><circle cx="11" cy="11" r="10" fill="none" stroke="#222" stroke-width="1"/><path d="M7 11h8M12 8l3 3-3 3" fill="none" stroke="#222" stroke-width="1"/></svg>
  <div class="svc" style="left:70px">
    <div class="svc-panel"></div>
    <div class="svc-photo" style="background:linear-gradient(160deg,#b9a48f,#3f5d55)" role="img" aria-label="Group of older adults seated in a class"></div>
    <div class="svc-week">WEEK 1</div><div class="svc-name">Training</div>
    <svg class="svc-icon" width="30" height="30" viewBox="0 0 30 30" fill="none" stroke="#fff" stroke-width="1.2"><rect x="10" y="3" width="17" height="12" rx="1"/><path d="M13 12l4-4 3 3 4-5"/><circle cx="6" cy="19" r="3"/><path d="M1 29v-4a5 5 0 0 1 10 0v4M14 29v-3a4 4 0 0 1 8 0v3"/><circle cx="18" cy="20" r="2.5"/></svg>
    <p class="svc-text">Excepteur sint occaecat cupidatat non proident, sunt in culpa qui officia deserunt mollit anim id est laborum.</p>
  </div>
  <div class="svc svc--active" style="left:284px">
    <div class="svc-panel"></div>
    <div class="svc-photo" style="background:linear-gradient(160deg,#d89a5c,#9a5c33)" role="img" aria-label="Older couple relaxing in a wooden sauna"></div>
    <div class="svc-week">WEEK 2</div><div class="svc-name">Sauna Use</div>
    <svg class="svc-icon" width="30" height="30" viewBox="0 0 30 30" fill="none" stroke="#fff" stroke-width="1.2"><rect x="2" y="14" width="26" height="14"/><path d="M2 19h26M2 24h26M9 14v14M15 14v14M21 14v14M11 10c-2-2 2-4 0-7M16 10c-2-2 2-4 0-7M21 10c-2-2 2-4 0-7"/></svg>
    <p class="svc-text">Excepteur sint occaecat cupidatat non proident, sunt in culpa qui officia deserunt mollit anim id est laborum.</p>
  </div>
  <div class="svc" style="left:498px">
    <div class="svc-panel"></div>
    <div class="svc-photo" style="background:linear-gradient(180deg,#8fa6b3,#4f6a78)" role="img" aria-label="Man immersed in a cold plunge pool"></div>
    <div class="svc-week">WEEK 3</div><div class="svc-name">Cold Plunge</div>
    <svg class="svc-icon" width="30" height="30" viewBox="0 0 30 30" fill="none" stroke="#fff" stroke-width="1.2"><path d="M2 16h26v4a7 7 0 0 1-7 7H9a7 7 0 0 1-7-7z"/><path d="M6 16V6a3 3 0 0 1 6 0M8 27l-1 2M22 27l1 2"/><rect x="19" y="2" width="9" height="9"/><path d="M23.5 2v9M19 6.5h9"/></svg>
    <p class="svc-text">Excepteur sint occaecat cupidatat non proident, sunt in culpa qui officia deserunt mollit anim id est laborum.</p>
  </div>

  <div class="abs quote">
    <svg class="quote-curve" width="758" height="261" viewBox="0 0 758 261"><path d="M0 70 C200 40 420 120 540 261 L758 261 L758 0 L0 0z" fill="rgba(255,255,255,.05)"/></svg>
  </div>
  <h2 class="abs heading quote-title">Get a Free Quote and Consultation</h2>
  <div class="rule" style="left:357px;top:1224px;background:#fff"></div>
  <p class="abs quote-text" style="top:1240px">Lorem ipsum dolor sit amet, consectetur adipiscing elit, sed do eiusmod tempor incididunt ut labore et dolore magna aliqua. Ut enim ad minim veniam, quis nostrud exercitation ullamco laboris nisi ut aliquip ex ea commodo consequat.</p>
  <p class="abs quote-text" style="top:1292px">Duis aute irure dolor in reprehenderit in voluptate velit esse cillum dolore eu fugiat nulla pariatur. Excepteur sint occaecat cupidatat non proident, sunt in culpa qui officia deserunt mollit anim id est laborum.</p>
  <div class="btn q-btn-light">Contact Us</div>
  <div class="btn q-btn-line">Call Us: +1 555 010 2480</div>

  <h2 class="abs heading center-title" style="top:1450px"><span class="accent">What</span> Customer Says</h2>
  <div class="rule" style="left:357px;top:1484px"></div>
  <div class="review" style="left:70px"><div class="avatar" role="img" aria-label="Portrait of reviewer"></div><div class="review-name">Daniel Hartwell</div><div class="stars">★★★★★</div><p class="review-text">Temporibus autem quibusdam et aut officiis debitis aut rerum necessitatibus saepe eveniet ut et voluptates</p></div>
  <div class="review" style="left:284px"><div class="avatar" role="img" aria-label="Portrait of reviewer"></div><div class="review-name">Steven Marlow</div><div class="stars">★★★★★</div><p class="review-text">Itaque earum rerum hic tenetur a sapiente delectus, reiciendis voluptatibus maiores alias consequatur aut</p></div>
  <div class="review" style="left:498px"><div class="avatar" role="img" aria-label="Portrait of reviewer"></div><div class="review-name">Emma Trent</div><div class="stars">★★★★★</div><p class="review-text">Nam libero tempore, cum soluta nobis est eligendi optio cumque nihil impedit quo minus id quod</p></div>
  <div class="abs pager"><i></i><i></i><i></i><i class="on"></i><i></i><i></i></div>

  <div class="abs footer"></div>
  <div class="field" style="left:70px">Name</div>
  <div class="field" style="left:196px">Email</div>
  <div class="field" style="left:321px">Phone Number</div>
  <div class="field" style="left:446px">Address</div>
  <div class="btn submit">Submit</div>
  <div class="fline" style="top:1876px"></div>
  <div class="abs f-brand">Amber Vital 480</div>
  <div class="abs f-col" style="left:287px"><h4>Quick Links</h4><ul><li>Home</li><li>About the Project</li><li>Services</li><li>Reviews</li><li>Contact Us</li></ul></div>
  <div class="abs f-col" style="left:426px"><h4>Help Links</h4><ul><li>FAQ</li><li>Terms of use</li><li>Privacy Policy</li><li>Support Links</li><li>Legal Notices</li></ul></div>
  <div class="abs f-col f-contact" style="left:545px"><h4>Contact Us</h4><ul>
    <li><span class="dot-ico"><svg width="9" height="11" viewBox="0 0 9 11"><path d="M4.5 0A4 4 0 0 0 .5 4c0 3 4 7 4 7s4-4 4-7a4 4 0 0 0-4-4z" fill="#fff"/><circle cx="4.5" cy="4" r="1.5" fill="#0a6cf0"/></svg></span><span>Amber Vital 480<br>Northfield</span></li>
    <li><span class="dot-ico"><svg width="10" height="10" viewBox="0 0 10 10"><path d="M2 .5l2 2-1 1.3a6 6 0 0 0 3.2 3.2L7.5 6l2 2-1.3 1.5C4.5 9.5.5 5.5.5 1.8z" fill="#fff"/></svg></span><span>+1 555 010 2480</span></li>
    <li><span class="dot-ico"><svg width="10" height="8" viewBox="0 0 10 8"><rect width="10" height="8" rx="1" fill="#fff"/><path d="M0.5 1l4.5 3.5L9.5 1" fill="none" stroke="#0a6cf0"/></svg></span><span>info@ambervital480.example</span></li>
  </ul></div>
  <div class="fline" style="top:2066px"></div>
  <div class="abs copy">Copyrights@2024.Amber Vital 480.All Rights Reserved</div>
</section>

<!-- Variant B -->
<section class="page page--b" aria-label="Home page, variant with office team photo">
  <div class="abs brand">Amber Vital 480</div>
  <nav class="abs nav"><a class="active" href="#">Home</a><a href="#">About</a><a href="#">Services</a><a href="#">Reviews</a><a href="#">Blog</a></nav>
  <div class="btn nav-cta">Contact Us</div>

  <div class="abs hero"></div>
  <div class="abs hero-vert">AMBER VITAL</div>
  <div class="abs hero-kicker">Welcome to</div>
  <h1 class="abs heading hero-title">Amber Vital 480</h1>
  <div class="abs hero-sub">9-WEEK PROGRAM WE CONDUCT</div>
  <div class="rule" style="left:70px;top:215px;width:40px"></div>
  <p class="abs hero-text">Lorem ipsum dolor sit amet, consectetur adipiscing elit, sed do eiusmod tempor incididunt ut labore et dolore magna aliqua.</p>
  <div class="btn hero-btn">Get Started</div>
  <div class="abs hero-photo photo-office" role="img" aria-label="Team of colleagues reviewing a tablet in an office"></div>

  <div class="tile" style="left:70px;top:442px;width:129px;height:258px;background:linear-gradient(160deg,#b08a66,#5e6f80)" role="img" aria-label="Coach meeting with a member at a laptop"></div>
  <div class="tile" style="left:203px;top:442px;width:128px;height:184px;background:linear-gradient(160deg,#c9c2b8,#8b7f70)" role="img" aria-label="Two women reviewing a tablet"></div>
  <div class="tile" style="left:203px;top:630px;width:128px;height:70px;background:linear-gradient(160deg,#a59a8f,#6b625a)" role="img" aria-label="Older couple embracing"></div>
  <h2 class="abs heading about-title"><span class="accent">About</span> Amber Vital 480</h2>
  <div class="rule" style="left:379px;top:467px;width:44px"></div>
  <p class="abs about-text" style="top:476px">Lorem ipsum dolor sit amet, consectetur adipiscing elit, sed do eiusmod incididunt ut labore et dolore magna aliqua. Ut enim ullamco laboris nisi aliquip ex ea commodoad minim venm, quis nostrud exercitation ullmco laboris nisi ut aliquip ex ea commodo consequat.</p>
  <p class="abs about-text" style="top:557px">Duis aute irure dolor in reprehenderit in voluptate velit esse cillum sunt culpa qui officia deserunt mollit anim id est laborum doloe eu fugiat nulla pariatur. Excepteur sint occaecat cupidatat non proident, sunt in culpa qui officia deserunt mollit anim id est laborum. Ut enim ad minim veniam, quis nostrud exercitation ullamco laboris nisi ut aliquip ex ea commodo consequat. Duis aute irure dolor in reprehenderit in voluptate velit esse cillum dolore eu fugiat nulla pariatur.</p>
  <div class="btn about-more">Read More</div>

  <div class="abs services"></div>
  <h2 class="abs heading center-title" style="top:788px"><span class="accent">Our</span> Services</h2>
  <div class="rule" style="left:357px;top:820px"></div>
  <svg class="arrow" style="left:23px" viewBox="0 0 22 22"><circle cx="11" cy="11" r="10" fill="none" stroke="#222" stroke-width="1"/><path d="M15 11H7M10 8l-3 3 3 3" fill="none" stroke="#222" stroke-width="1"/></svg>
  <svg class="arrow" style="left:710px" viewBox="0 0 22 22"><circle cx="11" cy="11" r="10" fill="none" stroke="#222" stroke-width="1"/><path d="M7 11h8M12 8l3 3-3 3" fill="none" stroke="#222" stroke-width="1"/></svg>
  <div class="svc" style="left:70px">
    <div class="svc-panel"></div>
    <div class="svc-photo" style="background:linear-gradient(160deg,#b9a48f,#3f5d55)" role="img" aria-label="Group of older adults seated in a class"></div>
    <div class="svc-week">WEEK 1</div><div class="svc-name">Training</div>
    <svg class="svc-icon" width="30" height="30" viewBox="0 0 30 30" fill="none" stroke="#fff" stroke-width="1.2"><rect x="10" y="3" width="17" height="12" rx="1"/><path d="M13 12l4-4 3 3 4-5"/><circle cx="6" cy="19" r="3"/><path d="M1 29v-4a5 5 0 0 1 10 0v4M14 29v-3a4 4 0 0 1 8 0v3"/><circle cx="18" cy="20" r="2.5"/></svg>
    <p class="svc-text">Excepteur sint occaecat cupidatat non proident, sunt in culpa qui officia deserunt mollit anim id est laborum.</p>
  </div>
  <div class="svc svc--active" style="left:284px">
    <div class="svc-panel"></div>
    <div class="svc-photo" style="background:linear-gradient(160deg,#d89a5c,#9a5c33)" role="img" aria-label="Older couple relaxing in a wooden sauna"></div>
    <div class="svc-week">WEEK 2</div><div class="svc-name">Sauna Use</div>
    <svg class="svc-icon" width="30" height="30" viewBox="0 0 30 30" fill="none" stroke="#fff" stroke-width="1.2"><rect x="2" y="14" width="26" height="14"/><path d="M2 19h26M2 24h26M9 14v14M15 14v14M21 14v14M11 10c-2-2 2-4 0-7M16 10c-2-2 2-4 0-7M21 10c-2-2 2-4 0-7"/></svg>
    <p class="svc-text">Excepteur sint occaecat cupidatat non proident, sunt in culpa qui officia deserunt mollit anim id est laborum.</p>
  </div>
  <div class="svc" style="left:498px">
    <div class="svc-panel"></div>
    <div class="svc-photo" style="background:linear-gradient(180deg,#8fa6b3,#4f6a78)" role="img" aria-label="Man immersed in a cold plunge pool"></div>
    <div class="svc-week">WEEK 3</div><div class="svc-name">Cold Plunge</div>
    <svg class="svc-icon" width="30" height="30" viewBox="0 0 30 30" fill="none" stroke="#fff" stroke-width="1.2"><path d="M2 16h26v4a7 7 0 0 1-7 7H9a7 7 0 0 1-7-7z"/><path d="M6 16V6a3 3 0 0 1 6 0M8 27l-1 2M22 27l1 2"/><rect x="19" y="2" width="9" height="9"/><path d="M23.5 2v9M19 6.5h9"/></svg>
    <p class="svc-text">Excepteur sint occaecat cupidatat non proident, sunt in culpa qui officia deserunt mollit anim id est laborum.</p>
  </div>

  <div class="abs quote">
    <svg class="quote-curve" width="758" height="261" viewBox="0 0 758 261"><path d="M0 70 C200 40 420 120 540 261 L758 261 L758 0 L0 0z" fill="rgba(255,255,255,.05)"/></svg>
  </div>
  <h2 class="abs heading quote-title">Get a Free Quote and Consultation</h2>
  <div class="rule" style="left:357px;top:1224px;background:#fff"></div>
  <p class="abs quote-text" style="top:1240px">Lorem ipsum dolor sit amet, consectetur adipiscing elit, sed do eiusmod tempor incididunt ut labore et dolore magna aliqua. Ut enim ad minim veniam, quis nostrud exercitation ullamco laboris nisi ut aliquip ex ea commodo consequat.</p>
  <p class="abs quote-text" style="top:1292px">Duis aute irure dolor in reprehenderit in voluptate velit esse cillum dolore eu fugiat nulla pariatur. Excepteur sint occaecat cupidatat non proident, sunt in culpa qui officia deserunt mollit anim id est laborum.</p>
  <div class="btn q-btn-light">Contact Us</div>
  <div class="btn q-btn-line">Call Us: +1 555 010 2480</div>

  <h2 class="abs heading center-title" style="top:1450px"><span class="accent">What</span> Customer Says</h2>
  <div class="rule" style="left:357px;top:1484px"></div>
  <div class="review" style="left:70px"><div class="avatar" role="img" aria-label="Portrait of reviewer"></div><div class="review-name">Daniel Hartwell</div><div class="stars">★★★★★</div><p class="review-text">Temporibus autem quibusdam et aut officiis debitis aut rerum necessitatibus saepe eveniet ut et voluptates</p></div>
  <div class="review" style="left:284px"><div class="avatar" role="img" aria-label="Portrait of reviewer"></div><div class="review-name">Steven Marlow</div><div class="stars">★★★★★</div><p class="review-text">Itaque earum rerum hic tenetur a sapiente delectus, reiciendis voluptatibus maiores alias consequatur aut</p></div>
  <div class="review" style="left:498px"><div class="avatar" role="img" aria-label="Portrait of reviewer"></div><div class="review-name">Emma Trent</div><div class="stars">★★★★★</div><p class="review-text">Nam libero tempore, cum soluta nobis est eligendi optio cumque nihil impedit quo minus id quod</p></div>
  <div class="abs pager"><i></i><i></i><i></i><i class="on"></i><i></i><i></i></div>

  <div class="abs footer"></div>
  <div class="field" style="left:70px">Name</div>
  <div class="field" style="left:196px">Email</div>
  <div class="field" style="left:321px">Phone Number</div>
  <div class="field" style="left:446px">Address</div>
  <div class="btn submit">Submit</div>
  <div class="fline" style="top:1876px"></div>
  <div class="abs f-brand">Amber Vital 480</div>
  <div class="abs f-col" style="left:287px"><h4>Quick Links</h4><ul><li>Home</li><li>About the Project</li><li>Services</li><li>Reviews</li><li>Contact Us</li></ul></div>
  <div class="abs f-col" style="left:426px"><h4>Help Links</h4><ul><li>FAQ</li><li>Terms of use</li><li>Privacy Policy</li><li>Support Links</li><li>Legal Notices</li></ul></div>
  <div class="abs f-col f-contact" style="left:545px"><h4>Contact Us</h4><ul>
    <li><span class="dot-ico"><svg width="9" height="11" viewBox="0 0 9 11"><path d="M4.5 0A4 4 0 0 0 .5 4c0 3 4 7 4 7s4-4 4-7a4 4 0 0 0-4-4z" fill="#fff"/><circle cx="4.5" cy="4" r="1.5" fill="#0a6cf0"/></svg></span><span>Amber Vital 480<br>Northfield</span></li>
    <li><span class="dot-ico"><svg width="10" height="10" viewBox="0 0 10 10"><path d="M2 .5l2 2-1 1.3a6 6 0 0 0 3.2 3.2L7.5 6l2 2-1.3 1.5C4.5 9.5.5 5.5.5 1.8z" fill="#fff"/></svg></span><span>+1 555 010 2480</span></li>
    <li><span class="dot-ico"><svg width="10" height="8" viewBox="0 0 10 8"><rect width="10" height="8" rx="1" fill="#fff"/><path d="M0.5 1l4.5 3.5L9.5 1" fill="none" stroke="#0a6cf0"/></svg></span><span>info@ambervital480.example</span></li>
  </ul></div>
  <div class="fline" style="top:2066px"></div>
  <div class="abs copy">Copyrights@2024.Amber Vital 480.All Rights Reserved</div>
</section>

</body>
</html>
```